Design my site www.brieflyledger.com

So here is what I am thinking in terms of design:

https://plenvo.com

https://www.skyluxair.com

http://kalvex.com/harbor-plaza-tower/

I want the theme to be white and blue (royal blue). I attached a paint picture of what I would like the site to look like in terms of placing the text. Generally, what I like about the sites above is that they are simple, you can navigate easily and have some kind of idea of what's going on by looking at the center (picture and motto). Let's establish a clear understanding of how the functional part of the site would look like. Please see the picture attached.

I want to keep it simple: On top would be the Name 'BRIEFLY ledger", somewhere to the right on top on the page would be 'Sign in" button.

In the center would be a picture (maybe a video) with the Motto (on top of it all in capital) OBSERVE NAVIGATE DECIDE and below would be the "sign up now"

Below the picture (like on kalvex.com site) or to the left on top of the page would be "About Us', "Press" "Contact Us' buttons.

Then once the user gets to his page his got 3 tabs " Press Headlines", "Events", " Briefings".

we would keep the same format I only have on the site, but separate for every Tab.

I do not want the user to get distracted. I also want him to be able to access the page though mobile phone and be able to get automatic updates just like Zorvan Pings without having to sign in daily.

The landing page must be minimalist yet with business/corporate feel where users can navigate easily and a "what you see is what you get" approach. You want an image or video (personally I prefer the video.. it does capture the users attention instantly, as long as it is an interesting video), with your taglines in it.

Sections available to public: About Us, Contact Us, Landing Page with Signup Option

Private: Public Sections + User Account Page, Tabs for (Events, Press Headlines, Briefings)

Target Market(s)

PR/media monitoring/diplomatic community

Coding

Coded - Design and coding required

Number of Pages Required

1 page

Font styles to use
Serif
Sans Serif

Colors
0255a3
ec1f27

Requirements
Must have
• a simple landing page, that is user friendly.
Nice to have
• a video with the explanation of how to navigate the site
Should not have
• too many colors, graphs etc.

```html
<!DOCTYPE html>
<html lang="en">
<head>
<meta charset="utf-8">
<title>BRIEFLY ledger — Briefings</title>
<link rel="stylesheet" href="https://fonts.googleapis.com/css2?family=Montserrat:wght@600;700&family=Open+Sans:wght@400;600&display=swap">
<style>
  :root {
    --brand-blue: #2b90c2;
    --brand-blue-dark: #2380b0;
    --ink: #3a3a3a;
    --ink-soft: #666;
    --panel-bg: #f5f5f5;
    --line: #dcdcdc;
    --white: #ffffff;
    --hero-top: #3b4a63;
    --hero-mid: #2a3445;
    --hero-low: #1c232d;
  }
  * { box-sizing: border-box; margin: 0; padding: 0; }
  html, body { width: 1200px; height: 896px; overflow: hidden; }
  body { position: relative; background: var(--white); font-family: "Open Sans", Arial, sans-serif; color: var(--ink); }

  .hero {
    position: absolute; left: 0; top: 0; width: 1200px; height: 257px;
    background: linear-gradient(180deg, var(--hero-top) 0%, #4a5569 22%, var(--hero-mid) 55%, var(--hero-low) 100%);
  }
  .brand {
    position: absolute; left: 99px; top: 39px; width: 320px; height: 57px;
    border: 3px solid var(--white);
    color: var(--white); font-family: "Montserrat", Arial, sans-serif; font-weight: 700;
    font-size: 30px; letter-spacing: -0.5px; display: flex; align-items: center; justify-content: center;
  }
  .sign-in {
    position: absolute; left: 982px; top: 51px; width: 83px; height: 32px;
    background: var(--brand-blue); border: 1px solid #7cc3e6; border-radius: 3px;
    color: var(--white); font-family: "Montserrat", Arial, sans-serif; font-weight: 700; font-size: 13px;
    display: flex; align-items: center; justify-content: center;
  }
  .menu-toggle { position: absolute; left: 1078px; top: 58px; }

  .tabs { position: absolute; left: 99px; top: 296px; width: 1002px; height: 42px; }
  .tab {
    position: absolute; top: 0; height: 42px; display: flex; align-items: center; justify-content: center;
    font-size: 15px; font-weight: 600; color: var(--ink); text-transform: uppercase;
  }
  .tab--press { left: 10px; width: 176px; }
  .tab--events { left: 260px; width: 120px; }
  .tab--active { left: 435px; width: 207px; background: var(--brand-blue); color: var(--white); }

  .panel {
    position: absolute; left: 99px; top: 338px; width: 1002px; height: 380px;
    background: var(--panel-bg); border: 1px solid var(--line); border-top: 1px solid var(--brand-blue);
  }
  .field-label { position: absolute; font-size: 13px; color: var(--ink-soft); }
  .field {
    position: absolute; left: 48px; width: 348px; height: 35px;
    background: var(--white); border: 1px solid var(--line); border-radius: 2px;
  }
  .field::after { content: ""; position: absolute; left: 311px; top: 0; bottom: 0; border-left: 1px solid #eee; }
  .field__value { position: absolute; left: 12px; top: 10px; font-size: 10px; color: var(--ink-soft); }
  .field__caret { position: absolute; left: 327px; top: 15px; }
  .submit {
    position: absolute; left: 49px; top: 276px; width: 128px; height: 37px;
    background: var(--brand-blue); color: var(--white); font-size: 15px; border-radius: 2px;
    display: flex; align-items: center; justify-content: center;
  }

  .sources { position: absolute; left: 425px; top: 79px; width: 348px; height: 172px; background: var(--white); border: 1px solid #cfcfcf; border-radius: 2px; }
  .sources__head { height: 35px; border-bottom: 1px solid #e3e3e3; position: relative; }
  .sources__head::after { content: ""; position: absolute; left: 311px; top: 0; bottom: 0; border-left: 1px solid #eee; }
  .check-row { position: absolute; left: 17px; display: flex; align-items: center; gap: 8px; font-size: 11.5px; color: var(--ink); }
  .check-row--head { top: 10px; font-size: 10px; color: var(--ink-soft); }
  .box { width: 10px; height: 10px; border: 1px solid #888; border-radius: 2px; background: #f2f2f2; position: relative; }
  .box svg { position: absolute; left: 1px; top: 0; }
  .scrollbar { position: absolute; left: 331px; top: 42px; width: 13px; height: 124px; background: #f1f1f1; }
  .scrollbar__thumb { position: absolute; left: 2px; top: 10px; width: 10px; height: 37px; background: #c1c1c1; }

  .footer { position: absolute; left: 0; top: 785px; width: 1200px; height: 111px; background: var(--panel-bg); border-top: 1px solid #e6e6e6; }
  .footer__nav { position: absolute; left: 99px; top: 37px; font-size: 12.5px; color: var(--brand-blue); }
  .footer__nav span.sep { color: var(--ink); margin: 0 11px; }
  .footer__copy { position: absolute; left: 98px; top: 64px; font-size: 12.5px; color: var(--ink); }
  .social { position: absolute; left: 927px; top: 35px; display: flex; gap: 9px; }
  .social__dot { width: 28px; height: 28px; border-radius: 50%; background: var(--brand-blue); }
</style>
</head>
<body>
  <header class="hero" role="img" aria-label="Dusk aerial photograph of a dense city skyline with lit towers">
    <div class="brand">BRIEFLY LEDGER</div>
    <div class="sign-in">SIGN IN</div>
    <svg class="menu-toggle" width="23" height="19" viewBox="0 0 23 19" aria-label="Menu">
      <rect x="0" y="0" width="23" height="4" fill="#fff"/>
      <rect x="0" y="7.5" width="23" height="4" fill="#fff"/>
      <rect x="0" y="15" width="23" height="4" fill="#fff"/>
    </svg>
  </header>

  <nav class="tabs">
    <div class="tab tab--press">Press Headlines</div>
    <div class="tab tab--events">Events</div>
    <div class="tab tab--active">Briefings</div>
  </nav>

  <main class="panel">
    <label class="field-label" style="left:48px;top:60px;">Daily briefings :</label>
    <div class="field" style="top:79px;"></div>

    <label class="field-label" style="left:48px;top:129px;">Driefing Date :</label>
    <div class="field" style="top:147px;"></div>

    <label class="field-label" style="left:48px;top:198px;">Daily Press Briefing :</label>
    <div class="field" style="top:216px;">
      <span class="field__value">Past 24 hours</span>
      <svg class="field__caret" width="9" height="5" viewBox="0 0 9 5"><path d="M0 0h9L4.5 5z" fill="#555"/></svg>
    </div>

    <div class="submit">SUBMIT</div>

    <label class="field-label" style="left:425px;top:60px;">Today's Briefing :</label>
    <div class="sources">
      <div class="sources__head">
        <div class="check-row check-row--head"><span class="box"><svg width="8" height="8" viewBox="0 0 8 8"><path d="M1 4l2 2 4-5" stroke="#333" stroke-width="1.4" fill="none"/></svg></span>All Sources</div>
      </div>
      <div class="check-row" style="top:52px;"><span class="box"><svg width="8" height="8" viewBox="0 0 8 8"><path d="M1 4l2 2 4-5" stroke="#333" stroke-width="1.4" fill="none"/></svg></span>United Kingdom</div>
      <div class="check-row" style="top:75px;"><span class="box"><svg width="8" height="8" viewBox="0 0 8 8"><path d="M1 4l2 2 4-5" stroke="#333" stroke-width="1.4" fill="none"/></svg></span>Iraq</div>
      <div class="check-row" style="top:98px;"><span class="box"><svg width="8" height="8" viewBox="0 0 8 8"><path d="M1 4l2 2 4-5" stroke="#333" stroke-width="1.4" fill="none"/></svg></span>Bahrain/region</div>
      <div class="check-row" style="top:120px;"><span class="box"><svg width="8" height="8" viewBox="0 0 8 8"><path d="M1 4l2 2 4-5" stroke="#333" stroke-width="1.4" fill="none"/></svg></span>Syria/region</div>
      <div class="check-row" style="top:143px;"><span class="box"><svg width="8" height="8" viewBox="0 0 8 8"><path d="M1 4l2 2 4-5" stroke="#333" stroke-width="1.4" fill="none"/></svg></span>Counterterrorism/iran</div>
      <div class="scrollbar">
        <svg style="position:absolute;left:3px;top:2px" width="7" height="4" viewBox="0 0 7 4"><path d="M0 4h7L3.5 0z" fill="#666"/></svg>
        <div class="scrollbar__thumb"></div>
        <svg style="position:absolute;left:3px;bottom:2px" width="7" height="4" viewBox="0 0 7 4"><path d="M0 0h7L3.5 4z" fill="#666"/></svg>
      </div>
    </div>
  </main>

  <footer class="footer">
    <div class="footer__nav">ABOUT US<span class="sep">/</span>PRESS<span class="sep">/</span>CONTACT US</div>
    <div class="footer__copy">2016 © Copyrights BRIEFLY ledger.All Rights Reserved</div>
    <div class="social" aria-label="Social links">
      <span class="social__dot"></span><span class="social__dot"></span><span class="social__dot"></span><span class="social__dot"></span><span class="social__dot"></span>
    </div>
  </footer>
</body>
</html>
```